Roadside building business signage for a holistic health clinic.

Replace signs as shown in the attached file. They are perforated stickers that go on the windows as shown. Looking for something that has our logo and says the name of the practice with logo (Fernridge Health & Wellness) also boldly says Acupuncture, IV Vitamins, and Holistic Health.
Possibly our phone number as well 318-562-7041
Updates

Please don't use pink except the logo. Earthy, organic tone colors appreciated.

Need of eye catching window signage of a holistic clinic on a brick building. Pink, purple, sage green, white color. Logo is pink on a white background. Please don't overload with too much pink. Words to include are "Fernridge Health and Wellness(name of business)", "Direct Primary Care", " Medical acupuncture", "IV Vitamin Therapy", "fernridgecareclinic.example","318-562-7041".

Target Market(s)

People will see in their cars passing by the building. Busy roadside so need to be visible while passing in fast speed.

Industry/Entity Type

Health & Wellness

Font styles to use
Sans Serif

Colors

Designer to choose colors to be used in the design.

Requirements
Must have
• On sign must have words Holistic Medicine, Medical Acupuncture, Direct Primary Care and IV vitamins.
Nice to have
• Simple, minimalistic, artistic yet has clear message. White, Black, Violet, Pink (logo), Dark green, Sage green.
Should not have
• Bold colors (red, yellow, blue), same tone colors. Blue waves on the current signage (uploaded file) must go.

```html
<!DOCTYPE html>
<html lang="en">
<head>
<meta charset="utf-8">
<title>Fernridge Health &amp; Wellness — Window Signage</title>
<link href="https://fonts.googleapis.com/css2?family=Jost:wght@400;500&display=swap" rel="stylesheet">
<style>
  :root {
    --backdrop: #ececec;
    --marble-light: #fbfcfb;
    --marble-mid: #eef1ef;
    --marble-vein: #dde3e0;
    --forest: #1f4a3a;
    --sage: #6f8f7a;
    --blossom: #d63a86;
    --shadow: rgba(0, 0, 0, 0.22);
  }
  * { box-sizing: border-box; margin: 0; padding: 0; }
  html, body {
    width: 1200px;
    height: 3720px;
    overflow: hidden;
    background: var(--backdrop);
  }
  .window-sign {
    position: absolute;
    left: 168px;
    width: 864px;
    height: 856px;
    box-shadow: 4px 6px 14px var(--shadow);
    overflow: hidden;
    font-family: "Jost", sans-serif;
    color: var(--forest);
  }
  .sign-logo { top: 1728px; }
  .sign-services { top: 2712px; }
  .marble-surface {
    position: absolute;
    inset: 0;
    background:
      linear-gradient(125deg, transparent 30%, var(--marble-vein) 34%, transparent 38%),
      linear-gradient(150deg, transparent 55%, var(--marble-vein) 58%, transparent 62%),
      linear-gradient(160deg, var(--marble-light) 0%, var(--marble-mid) 50%, var(--marble-light) 100%);
  }
  .brand {
    position: absolute;
    left: 0;
    right: 0;
    display: flex;
    flex-direction: column;
    align-items: center;
  }
  .brand-mark { border-radius: 50%; background: var(--blossom); }
  .brand-name { text-align: center; line-height: 1; }
  .brand-name .name-main { display: block; font-weight: 500; letter-spacing: 0.08em; }
  .brand-name .name-sub { display: block; font-weight: 400; letter-spacing: 0.24em; }

  .sign-logo .brand { top: 200px; }
  .sign-logo .brand-mark { width: 190px; height: 190px; margin-bottom: 56px; }
  .sign-logo .name-main { font-size: 104px; }
  .sign-logo .name-sub { font-size: 30px; margin-top: 22px; }

  .sign-services .brand { top: 56px; }
  .sign-services .brand-mark { width: 120px; height: 120px; margin-bottom: 24px; }
  .sign-services .name-main { font-size: 72px; }
  .sign-services .name-sub { font-size: 22px; margin-top: 12px; }

  .service-list {
    position: absolute;
    left: 150px;
    top: 372px;
    list-style: none;
    display: flex;
    flex-direction: column;
    gap: 24px;
  }
  .service {
    display: flex;
    align-items: center;
    gap: 26px;
    font-weight: 500;
    font-size: 44px;
    line-height: 1;
  }
  .service-icon { width: 66px; height: 66px; flex: none; }
  .contact-line {
    position: absolute;
    left: 0;
    right: 0;
    bottom: 48px;
    text-align: center;
    font-size: 28px;
    font-weight: 400;
    letter-spacing: 0.04em;
    color: var(--sage);
  }
  .contact-line .divider { margin: 0 16px; color: var(--blossom); }
</style>
</head>
<body>
  <main>
    <section class="window-sign sign-logo">
      <div class="marble-surface" role="img" aria-label="White marble texture with soft grey-green veins"></div>
      <div class="brand">
        <span class="brand-mark"></span>
        <p class="brand-name"><span class="name-main">FERNRIDGE</span><span class="name-sub">HEALTH &amp; WELLNESS</span></p>
      </div>
    </section>

    <section class="window-sign sign-services">
      <div class="marble-surface" role="img" aria-label="White marble texture with soft grey-green veins"></div>
      <div class="brand">
        <span class="brand-mark"></span>
        <p class="brand-name"><span class="name-main">FERNRIDGE</span><span class="name-sub">HEALTH &amp; WELLNESS</span></p>
      </div>
      <ul class="service-list">
        <li class="service">
          <svg class="service-icon" viewBox="0 0 76 76" aria-hidden="true">
            <circle cx="38" cy="38" r="34" fill="none" stroke="#d63a86" stroke-width="4"/>
            <path d="M32 22h12v10h10v12H44v10H32V44H22V32h10z" fill="#1f4a3a"/>
          </svg>
          Direct Primary Care
        </li>
        <li class="service">
          <svg class="service-icon" viewBox="0 0 76 76" aria-hidden="true">
            <circle cx="38" cy="38" r="34" fill="none" stroke="#d63a86" stroke-width="4"/>
            <line x1="24" y1="52" x2="52" y2="24" stroke="#1f4a3a" stroke-width="4" stroke-linecap="round"/>
            <circle cx="52" cy="24" r="5" fill="#1f4a3a"/>
          </svg>
          Medical Acupuncture
        </li>
        <li class="service">
          <svg class="service-icon" viewBox="0 0 76 76" aria-hidden="true">
            <circle cx="38" cy="38" r="34" fill="none" stroke="#d63a86" stroke-width="4"/>
            <path d="M38 18 C30 32 26 38 26 45 a12 12 0 0 0 24 0 C50 38 46 32 38 18 Z" fill="#1f4a3a"/>
          </svg>
          IV Vitamins
        </li>
        <li class="service">
          <svg class="service-icon" viewBox="0 0 76 76" aria-hidden="true">
            <circle cx="38" cy="38" r="34" fill="none" stroke="#d63a86" stroke-width="4"/>
            <path d="M22 54 C22 32 36 22 56 20 C54 40 44 54 22 54 Z" fill="#1f4a3a"/>
            <line x1="22" y1="54" x2="44" y2="32" stroke="#fbfcfb" stroke-width="3"/>
          </svg>
          Holistic Medicine
        </li>
      </ul>
      <p class="contact-line">318-562-7041<span class="divider">•</span>fernridgecareclinic.example</p>
    </section>
  </main>
</body>
</html>
```